Architectural, Engineering and Design Build

Tovandex4.com
Veteran Disabled Certified company is doing business in Architecture, Engineer and Design build - look simialr websites and come up with design follow following website
https://hollis-darnet.example/
https://www.venlorcogroup.example/
https://www.pembrisgc.example/contract-vehicles/service-disabled-veteran-owned-small-business-sdvosb/
https://www.corbelnetlink.example/about/sdvosb/

Target Market(s)

US - Defense and Federal Government

Industry/Entity Type

Colors
0054AA
0677BA
7BADD7
CADEEF
E8F1F8

Requirements
Must have
• Army, American patriotism , Buildings, construction, architecture, engineering
Nice to have
• I need to attract federal government agencies and Defense

```html
<!DOCTYPE html>
<html lang="en">
<head>
<meta charset="utf-8">
<title>Tovandex4 — Planning, Design &amp; Construction</title>
<link href="https://fonts.googleapis.com/css2?family=Montserrat:wght@500;600;700;800&family=Roboto:ital,wght@0,400;0,500;0,700;1,400&display=swap" rel="stylesheet">
<style>
:root{
  --navy:#0b2f6e;
  --navy-deep:#0a2a63;
  --blue:#0054aa;
  --blue-mid:#0677ba;
  --sky:#7badd7;
  --mist:#cadeef;
  --ice:#e8f1f8;
  --red:#d9141f;
  --ink:#2b2f36;
  --body:#3a3d44;
  --grey-bg:#eceef1;
  --white:#ffffff;
}
*{box-sizing:border-box;margin:0;padding:0}
html,body{width:1200px;height:3852px;overflow:hidden}
body{position:relative;font-family:"Roboto",Arial,sans-serif;color:var(--ink);background:var(--white)}
h1,h2,h3,h4,p{font-size:inherit;font-weight:inherit}
.heading{font-family:"Montserrat",Arial,sans-serif;font-weight:800;letter-spacing:4px;text-transform:uppercase;color:var(--navy)}
.btn{display:inline-block;background:var(--red);color:var(--white);font-family:"Montserrat",Arial,sans-serif;font-weight:700;font-size:15px;letter-spacing:1px;text-transform:uppercase;text-align:center;line-height:50px;height:50px;width:176px}
.btn--navy{background:var(--navy)}
.rule{display:block;width:56px;height:4px;background:var(--navy);margin:12px auto 0}
.section{position:absolute;left:0;width:1200px;overflow:hidden}
.photo{position:absolute}

/* header */
.site-header{top:0;height:69px;background:var(--white);z-index:5;overflow:visible;box-shadow:0 1px 0 #e6e8ec}
.brand{position:absolute;left:102px;top:-20px;width:130px;height:130px;border-radius:50%;background:var(--white);display:flex;align-items:center;justify-content:center;gap:6px;padding-top:20px;box-shadow:0 3px 8px rgba(0,0,0,.1)}
.brand-dot{width:12px;height:12px;border-radius:50%;background:var(--red)}
.brand-name{font-family:"Montserrat",Arial,sans-serif;font-weight:800;font-size:17px;color:var(--navy);letter-spacing:.5px}
.main-nav{position:absolute;left:375px;top:30px;display:flex;gap:70px}
.main-nav a{font-family:"Montserrat",Arial,sans-serif;font-weight:600;font-size:12.5px;letter-spacing:1.3px;color:var(--ink);text-decoration:none;text-transform:uppercase;position:relative}
.main-nav a.active::after{content:"";position:absolute;left:0;right:0;bottom:-9px;height:2px;background:var(--red)}

/* hero */
.hero{top:69px;height:621px}
.hero .photo{inset:0;background:
  linear-gradient(90deg,rgba(24,50,130,.95) 0%,rgba(32,64,150,.85) 30%,rgba(40,80,160,.35) 55%,rgba(0,0,0,0) 70%),
  radial-gradient(ellipse 260px 140px at 620px 90px,rgba(255,255,255,.8),rgba(255,255,255,0)),
  radial-gradient(ellipse 420px 600px at 1020px 420px,#c7ccd2 0%,#a8aeb6 45%,rgba(140,150,160,0) 75%),
  linear-gradient(180deg,#5f8fd0 0%,#8fb4e0 45%,#b0c3d8 100%)}
.hero-eyebrow{position:absolute;left:112px;top:193px;color:var(--white);font-family:"Montserrat",Arial,sans-serif;font-size:18px;letter-spacing:3px;font-weight:500}
.hero-title{position:absolute;left:112px;top:218px;color:var(--white);font-size:43px;line-height:48px;letter-spacing:4px}
.hero .btn{position:absolute;left:117px;top:329px;height:48px;line-height:48px}
.slider-dots{position:absolute;left:552px;top:571px;display:flex;gap:6px;align-items:center}
.slider-dots span{width:8px;height:8px;border-radius:50%;background:rgba(255,255,255,.5)}
.slider-dots span.on{background:var(--white)}
.slider-dots .arrow{width:18px;height:18px;background:var(--white);display:flex;align-items:center;justify-content:center}

/* about */
.about{top:690px;height:564px;background:linear-gradient(90deg,#f1f3f6,#ffffff 60%)}
.about .photo{left:0;top:0;width:583px;height:562px;background:
  radial-gradient(ellipse 200px 90px at 80px 180px,rgba(255,255,255,.85),rgba(255,255,255,0)),
  linear-gradient(90deg,rgba(0,0,0,0) 0%,rgba(0,0,0,0) 16%,rgba(40,110,190,.85) 20%,rgba(60,140,215,.9) 50%,rgba(35,100,170,.85) 82%,rgba(0,0,0,0) 86%),
  linear-gradient(180deg,#4f8fd6 0%,#8fbfea 45%,#6c9a5a 78%,#5f8a4f 84%,#b8bcc0 90%,#9ea3a8 100%)}
.about-flag{position:absolute;right:0;top:0;width:120px;height:564px;background:linear-gradient(165deg,rgba(255,255,255,0) 35%,rgba(0,84,170,.85) 42%,rgba(0,84,170,.85) 52%,#f3f3f3 56%,var(--red) 62%,var(--red) 100%)}
.about-body{position:absolute;left:651px;top:110px;width:470px}
.about-body h2{font-size:32px;letter-spacing:4px}
.about-body p{font-size:15.5px;line-height:22px;margin-top:22px;color:var(--body)}
.about-body h2+p{margin-top:40px}
.about .btn{position:absolute;left:647px;top:412px}

/* services */
.services-title{top:1312px;text-align:center}
.services-title h2,.projects-title h2{font-size:30px;line-height:38px}
.services-grid{top:1403px;height:320px;display:flex;gap:3px}
.service{position:relative;flex:1;height:320px;overflow:hidden}
.service .photo{inset:0}
.service-label{position:absolute;left:0;right:0;bottom:26px;text-align:center;color:var(--white);font-family:"Montserrat",Arial,sans-serif;font-weight:700;font-size:20px;letter-spacing:1.5px}
.service-label .rule{background:var(--white);width:56px;height:3px;margin-top:8px}
.service--feature{background:linear-gradient(160deg,#e2343c,#d9141f 60%,#c9121c);color:var(--white);text-align:center;padding:76px 34px 0}
.service--feature h3{font-family:"Montserrat",Arial,sans-serif;font-weight:700;font-size:20px;letter-spacing:1.5px}
.service--feature .rule{background:var(--white);height:2px;width:56px;margin:10px auto 20px}
.service--feature p{font-size:15px;line-height:21px}
.service--feature .btn{margin-top:12px;width:176px}

/* how */
.how{top:1731px;height:543px;background:var(--grey-bg)}
.how .photo{right:0;top:0;width:760px;height:543px;background:
  radial-gradient(ellipse 160px 110px at 190px 400px,rgba(255,255,255,.95),rgba(255,255,255,0)),
  radial-gradient(ellipse 120px 80px at 560px 120px,rgba(40,44,52,.55),rgba(40,44,52,0)),
  radial-gradient(ellipse 180px 120px at 700px 480px,rgba(58,92,150,.7),rgba(58,92,150,0)),
  linear-gradient(90deg,var(--grey-bg) 0%,#e6eaf0 22%,#d8dee8 50%,#cbd3de 80%,#b9c3d1 100%)}
.how-body{position:absolute;left:112px;top:136px;width:430px}
.how-body h2{font-size:32px;line-height:40px;letter-spacing:4px}
.how-body .rule{margin:8px 0 0;width:80px}
.how-body p{font-size:15.5px;line-height:22px;margin-top:28px;color:var(--body)}
.how .btn{position:absolute;left:108px;top:349px}

/* projects */
.projects-title{top:2318px;text-align:center}
.project-grid{position:absolute;left:100px;top:2406px;display:flex;gap:7px}
.project{width:327px;height:329px;background:var(--ice)}
.project .photo{position:relative;width:327px;height:225px}
.project-cat{font-family:"Montserrat",Arial,sans-serif;font-weight:700;font-size:11px;letter-spacing:1.3px;color:var(--navy);margin:16px 0 0 33px;text-transform:uppercase}
.project-text{font-family:"Montserrat",Arial,sans-serif;font-weight:600;font-size:14px;line-height:22px;color:#2e3a52;margin:4px 30px 0 33px}

/* success */
.success{top:2810px;height:532px}
.success .photo{inset:0;background:
  radial-gradient(ellipse 60px 90px at 915px 270px,rgba(255,200,120,.9),rgba(255,200,120,0)),
  radial-gradient(ellipse 260px 140px at 980px 160px,#a7a29b,rgba(167,162,155,0)),
  linear-gradient(180deg,#7f93bd 0%,#b9c3d6 35%,#d4d0c8 60%,#8b8f94 82%,#3e4a56 100%)}
.success-panel{position:absolute;inset:0;background:linear-gradient(90deg,#c8141c,#e01018 60%);clip-path:polygon(0 0,678px 0,480px 532px,0 532px)}
.success-body{position:absolute;left:121px;top:96px;width:390px;color:var(--white)}
.success-body h2{color:var(--white);font-size:28px;line-height:34px;letter-spacing:4px}
.success-body h3{font-family:"Montserrat",Arial,sans-serif;font-weight:600;font-size:17px;line-height:22px;margin-top:30px;text-transform:uppercase}
.success-body p{font-style:italic;font-size:14.5px;line-height:22px;margin-top:14px}
.stars{display:flex;margin-top:12px}
.slider-bar{display:flex;gap:8px;margin-top:32px}
.slider-bar span{width:36px;height:3px;background:rgba(255,255,255,.3)}
.slider-bar span.on{background:var(--sky)}

/* contact strip */
.cta{top:3342px;height:123px;background:linear-gradient(90deg,#efc9cd 0%,#f7e6e8 8%,#ffffff 16%,#ffffff 82%,#f7e6e8 92%,#efc9cd 100%)}
.cta h2{position:absolute;left:145px;top:44px;font-size:26px;line-height:32px;letter-spacing:4px}
.cta .btn{position:absolute;left:853px;top:34px;width:177px;height:52px;line-height:52px}

/* footer */
.site-footer{top:3465px;height:387px;background:var(--navy-deep);color:var(--white)}
.footer-flag{position:absolute;left:0;top:0;width:440px;height:387px;background:linear-gradient(155deg,rgba(0,0,0,0) 35%,rgba(217,20,31,.45) 48%,rgba(255,255,255,.2) 55%,rgba(217,20,31,.45) 62%,rgba(255,255,255,.2) 69%,rgba(217,20,31,.4) 76%,rgba(0,0,0,0) 90%)}
.footer-col{position:absolute;top:80px}
.footer-col h4{font-family:"Montserrat",Arial,sans-serif;font-weight:700;font-size:15px;letter-spacing:.3px;text-transform:uppercase;margin-bottom:14px}
.footer-col li{list-style:none;font-size:13px;margin-bottom:14px}
.contact-line{display:flex;gap:12px;font-size:13px;line-height:16px;margin-bottom:16px}
.social{display:flex;gap:7px}
.social span{width:39px;height:39px;border:2px solid var(--white);border-radius:50%;display:flex;align-items:center;justify-content:center}
.social span::after{content:"";width:12px;height:12px;border-radius:50%;background:var(--white)}
.copyright{position:absolute;left:0;right:0;bottom:14px;text-align:center;font-size:11.5px;color:rgba(255,255,255,.8)}
</style>
</head>
<body>

<header class="section site-header">
  <div class="brand"><span class="brand-dot"></span><span class="brand-name">TOVANDEX4</span></div>
  <nav class="main-nav">
    <a class="active">About Us</a><a>Services</a><a>Projects</a><a>Career</a><a>News</a><a>Contact Us</a>
  </nav>
</header>

<section class="section hero">
  <div class="photo" role="img" aria-label="Low-angle view of a concrete high-rise under construction with a tower crane, blue sky and a faint American flag overlay"></div>
  <p class="hero-eyebrow">WELCOME TO TOVANDEX4</p>
  <h1 class="heading hero-title" style="color:#fff">Planning, Design<br>&amp; Construction</h1>
  <a class="btn">Learn More</a>
  <div class="slider-dots">
    <span class="arrow"><svg width="8" height="10" viewBox="0 0 8 10"><path d="M6 1 2 5l4 4" stroke="#0b2f6e" stroke-width="2" fill="none"/></svg></span>
    <span class="on"></span><span></span><span></span><span></span>
    <span class="arrow"><svg width="8" height="10" viewBox="0 0 8 10"><path d="M2 1l4 4-4 4" stroke="#0b2f6e" stroke-width="2" fill="none"/></svg></span>
  </div>
</section>

<section class="section about">
  <div class="photo" role="img" aria-label="Modern glass office building with trees and a clear blue sky"></div>
  <div class="about-flag" role="img" aria-label="Corner of a waving American flag"></div>
  <div class="about-body">
    <h2 class="heading">About Tovandex4</h2>
    <p>Lorem ipsum dolor sit amet, consectetur adipiscing elit, sed do eiusmod tempor incididunt ut labore et dolore magna aliqua. Ut enim ad minim veniam, quis nostrud exercitation ullamco laboris nisi ut aliquip ex ea commodo consequat.</p>
    <p>Duis aute irure dolor in reprehenderit in voluptate velit esse cillum dolore eu fugiat nulla pariatur. Excepteur sint occaecat cupidatat non proident, sunt in culpa qui officia deserunt mollit anim id est laborum.</p>
  </div>
  <a class="btn">Learn More</a>
</section>

<section class="section services-title"><h2 class="heading">Services We Provide</h2><span class="rule"></span></section>

<section class="section services-grid">
  <article class="service">
    <div class="photo" role="img" aria-label="Hand holding a 3D building model over architectural sketches" style="background:radial-gradient(ellipse 130px 80px at 200px 150px,#6e5a48,rgba(110,90,72,0)),linear-gradient(180deg,#eef2f6 0%,#d6dee7 50%,#9fb0c4 85%,#7f93ad 100%)"></div>
    <h3 class="service-label">ARCHITECTURE<span class="rule"></span></h3>
  </article>
  <article class="service service--feature">
    <h3>ENGINEER AND DESIGN</h3><span class="rule"></span>
    <p>Lorem ipsum dolor sit amet, consectetur adipiscing elit, sed do eiusmod tempor incididunt ut labore et dolore magna aliqua. Ut enim ad minim veni</p>
    <a class="btn btn--navy">Learn More</a>
  </article>
  <article class="service">
    <div class="photo" role="img" aria-label="Engineers reviewing plans on a tablet at a desk" style="background:radial-gradient(ellipse 80px 50px at 250px 40px,#d9b34a,rgba(217,179,74,0)),radial-gradient(ellipse 150px 90px at 200px 160px,#c8ccd2,rgba(200,204,210,0)),linear-gradient(160deg,#3b4b60,#5f7088 50%,#8796aa)"></div>
    <h3 class="service-label">PROJECT MANAGEMENT<span class="rule"></span></h3>
  </article>
</section>

<section class="section how">
  <div class="photo" role="img" aria-label="Hands working over blueprints with a hard hat, calculator and rolled drawings"></div>
  <div class="how-body">
    <h2 class="heading">How We Work</h2><span class="rule"></span>
    <p>Lorem ipsum dolor sit amet, consectetur adipiscing elit, sed do eiusmod tempor incididunt ut labore et dolore magna aliqua. Ut enim ad minim veniam, quis nostrud exercitation ullamco laboris nisi ut aliquip ex ea commodo consequat. uis aute irure dolor</p>
  </div>
  <a class="btn">Learn More</a>
</section>

<section class="section projects-title"><h2 class="heading">Recent Projects</h2><span class="rule"></span></section>

<div class="project-grid">
  <article class="project">
    <div class="photo" role="img" aria-label="Looking up between two brick towers joined by a bridge" style="background:linear-gradient(90deg,#5a2f1b,#8c4d2c 25%,#b06a3e 38%,#a9d6e6 46%,#c2e2ec 54%,#b06a3e 62%,#8c4d2c 75%,#5a2f1b)"></div>
    <p class="project-cat">Architecture</p>
    <p class="project-text">Lorem ipsum dolor sit amet consectetur adipiscing elit</p>
  </article>
  <article class="project">
    <div class="photo" role="img" aria-label="Curved facade of a modern building with blue and red panels" style="background:linear-gradient(170deg,#9fb3cd 0%,#6f8fb5 25%,#1f2f48 45%,#3b5f95 60%,#8a3c48 72%,#2c4e84 85%,#6f8fb5)"></div>
    <p class="project-cat">Engineer &amp; Design</p>
    <p class="project-text">Lorem ipsum dolor sit amet consectetur adipiscing elit</p>
  </article>
  <article class="project">
    <div class="photo" role="img" aria-label="Timber-clad modern building against a teal sky" style="background:radial-gradient(ellipse 140px 110px at 250px 110px,#cfa57a,rgba(207,165,122,0)),linear-gradient(180deg,#5d9da2 0%,#8dbcbc 40%,#dcc2a0 62%,#c9a57c 100%)"></div>
    <p class="project-cat">Architecture</p>
    <p class="project-text">Lorem ipsum dolor sit amet consectetur adipiscing elit</p>
  </article>
</div>

<section class="section success">
  <div class="photo" role="img" aria-label="Modern concrete house at dusk blending into a wireframe architectural sketch"></div>
  <div class="success-panel"></div>
  <div class="success-body">
    <h2 class="heading">Success Stories</h2>
    <h3>Sed ut perspiciatis unde omnis iste natus error sit</h3>
    <p>Lorem ipsum dolor sit amet, consectetur adipiscing elit, sed do eiusmod tempor incididunt ut labore et dolore magna aliqua. Ut enim ad minim veniam, quis nostrud exercitation ullamco laboris nisi ut aliquip ex ea commodo consequat. Duis aute irure dolor in reprehenderit in voluptate velit esse cillum dolore eu fugiat</p>
    <div class="stars">
      <svg width="110" height="20" viewBox="0 0 110 20" aria-label="Five stars"><g fill="#f4c02a"><path id="st" d="M10 1l2.6 6 6.4.5-4.9 4.2 1.5 6.3L10 14.6 4.4 18l1.5-6.3L1 7.5 7.4 7z"/><use href="#st" x="22"/><use href="#st" x="44"/><use href="#st" x="66"/><use href="#st" x="88"/></g></svg>
    </div>
    <div class="slider-bar"><span class="on"></span><span></span><span></span></div>
  </div>
</section>

<section class="section cta">
  <h2 class="heading">Contact Us Today To Get Started</h2>
  <a class="btn">Contact Us</a>
</section>

<footer class="section site-footer">
  <div class="footer-flag" role="img" aria-label="Waving American flag in the corner"></div>
  <div class="footer-col" style="left:151px"><h4>Navigation</h4><ul><li>Home</li><li>About Us</li><li>Services</li><li>Why Us</li><li>Carer</li></ul></div>
  <div class="footer-col" style="left:379px"><h4>Resources</h4><ul><li>Projects</li><li>Blogs</li><li>Terms of Use</li><li>Contact Us</li></ul></div>
  <div class="footer-col" style="left:618px"><h4>Contact Us</h4>
    <div class="contact-line"><svg width="16" height="20" viewBox="0 0 16 20"><path d="M8 0a7 7 0 0 0-7 7c0 5 7 13 7 13s7-8 7-13a7 7 0 0 0-7-7zm0 10a3 3 0 1 1 0-6 3 3 0 0 1 0 6z" fill="#fff"/></svg><span>Larkmoor Avenue 41<br>2210 Fenwick Ridge</span></div>
    <div class="contact-line"><svg width="16" height="16" viewBox="0 0 24 24"><path d="M6.6 10.8a15 15 0 0 0 6.6 6.6l2.2-2.2a1 1 0 0 1 1-.25 11 11 0 0 0 3.6.6 1 1 0 0 1 1 1V20a1 1 0 0 1-1 1A17 17 0 0 1 3 4a1 1 0 0 1 1-1h3.5a1 1 0 0 1 1 1c0 1.2.2 2.4.6 3.6a1 1 0 0 1-.25 1z" fill="#fff"/></svg><span>(555) 014-2290</span></div>
    <div class="contact-line"><svg width="18" height="14" viewBox="0 0 18 14"><rect width="18" height="14" rx="1" fill="#fff"/><path d="M1 1l8 6 8-6" stroke="#0a2a63" stroke-width="1.5" fill="none"/></svg><span>info@tovandex4.example</span></div>
  </div>
  <div class="footer-col" style="left:893px;top:86px"><h4>Follow Us</h4><div class="social"><span aria-label="Social profile one"></span><span aria-label="Social profile two"></span><span aria-label="Social profile three"></span></div></div>
  <p class="copyright">© 2024 Company Name. All Rights Reserved</p>
</footer>

</body>
</html>
```